Business Card Design

We provide services doing multiple jobs in the construction industry.Please note: The company name needs to be ROCK SOLID BUILDING SERVICESAttached logo was an example of what we wanted. Can you change up the colors?

Industry/Entity Type

Construction

Contact Information for Business Card

ROCK SOLID BUILDING SERVICES5401 HUDSON BEND RDAUSTIN, TX 78734(512)243-6854ROCKSOLIDBUILDINGSERVICES@GMAIL.COM

```html
<!DOCTYPE html>
<html lang="en">
<head>
<meta charset="utf-8">
<title>Pearlwood Framing Works – Business Card</title>
<link href="https://fonts.googleapis.com/css2?family=Oswald:wght@700&family=Arimo:wght@400&display=swap" rel="stylesheet">
<style>
  :root {
    --page-bg: #e7e6e3;
    --card-white: #ffffff;
    --navy: #211f5e;
    --ink-light: #ffffff;
    --shadow: rgba(0, 0, 0, 0.22);
  }
  * { margin: 0; padding: 0; box-sizing: border-box; }
  html, body {
    width: 1200px;
    height: 848px;
    overflow: hidden;
    background: var(--page-bg);
  }
  .stage {
    position: relative;
    width: 1200px;
    height: 848px;
  }
  .card {
    position: absolute;
    left: 130px;
    top: 164px;
    width: 940px;
    height: 520px;
    border-radius: 30px;
    overflow: hidden;
    background: var(--card-white);
    box-shadow: 0 18px 40px var(--shadow);
  }
  .card-bands {
    position: absolute;
    inset: 0;
  }
  .brand-mark {
    position: absolute;
    left: 40px;
    top: 190px;
    width: 290px;
    display: flex;
    align-items: center;
    gap: 14px;
  }
  .brand-mark-square {
    flex: none;
    width: 26px;
    height: 26px;
    background: var(--navy);
  }
  .brand-mark-name {
    font-family: "Oswald", sans-serif;
    font-weight: 700;
    font-size: 34px;
    line-height: 1.05;
    color: var(--navy);
    letter-spacing: 0.5px;
  }
  .company-title {
    position: absolute;
    right: 60px;
    top: 62px;
    text-align: center;
    color: var(--ink-light);
  }
  .company-name {
    font-family: "Oswald", sans-serif;
    font-weight: 700;
    font-size: 50px;
    line-height: 1;
    letter-spacing: 1px;
  }
  .company-tagline {
    font-family: "Arimo", sans-serif;
    font-size: 17px;
    letter-spacing: 1px;
    margin-top: 4px;
  }
  .contact {
    position: absolute;
    left: 400px;
    right: 40px;
    top: 322px;
    color: var(--ink-light);
    font-family: "Arimo", sans-serif;
    font-style: normal;
    font-size: 18px;
    line-height: 1.7;
    letter-spacing: 0.3px;
    white-space: nowrap;
  }
  .contact-phone { padding-left: 170px; }
</style>
</head>
<body>
  <main class="stage">
    <article class="card">
      <svg class="card-bands" width="940" height="520" viewBox="0 0 940 520" aria-hidden="true">
        <polygon points="420,0 940,0 940,520 340,520" fill="var(--navy)"/>
        <line x1="406" y1="0" x2="326" y2="520" stroke="var(--navy)" stroke-width="4"/>
      </svg>

      <div class="brand-mark">
        <span class="brand-mark-square"></span>
        <span class="brand-mark-name">PEARLWOOD<br>FRAMING WORKS</span>
      </div>

      <header class="company-title">
        <h1 class="company-name">PEARLWOOD</h1>
        <p class="company-tagline">FRAMING WORKS</p>
      </header>

      <address class="contact">
        <div class="contact-phone">(512)555-0193</div>
        <div class="contact-address">7732 FERNGLEN PASS LN AUSTIN,TX 78734</div>
        <div class="contact-email">PEARLWOODFRAMINGWORKS@MAILNEST.EXAMPLE</div>
      </address>
    </article>
  </main>
</body>
</html>
```